Business cards for a fun web development agency

Hi,I am building a web development agency. You can read about it on the website http://kite-loft.examplehost.com. Basically, I want to focus on free and open source products and stay as far away from the corporate business feeling as possible. I want to build a community so I want the business card to feel fun and approachable (at the risk of professional if need be). I am uploading some of my image assets in various file formats. Feel free to use them or make your own if you want just keeping in theme with the website.
Industry/Entity Type
Building
Contact Information for Business Card
Company Name: Boat ShedWebsite: www.kiteloftdev.example (it's currently in alpha on http://kite-loft.examplehost.com if you want to see the them we are trying to capture)My name is: Banner B. SchaferMy email: banner@boatsheddev.comMy phone: 0431 587 904
Look and feel

```html
<!DOCTYPE html>
<html lang="en">
<head>
<meta charset="utf-8">
<title>Kite Loft — Business Cards</title>
<link rel="stylesheet" href="https://fonts.googleapis.com/css2?family=Exo+2:wght@400;600&display=swap">
<style>
  :root {
    --brand-blue: #1384b5;
    --swoosh-grey: #8c8d8f;
    --card-white: #ffffff;
    --backdrop: #d9d9d9;
    --ink-white: #ffffff;
  }
  * { margin: 0; padding: 0; box-sizing: border-box; }
  html, body { width: 1200px; height: 771px; overflow: hidden; }
  body {
    background: var(--backdrop);
    font-family: "Exo 2", Arial, sans-serif;
    position: relative;
  }
  .card {
    position: absolute;
    top: 231px;
    width: 540px;
    height: 309px;
    background: var(--card-white);
    overflow: hidden;
  }
  .card--front { left: 40px; }
  .card--back { left: 620px; }

  .wordmark {
    display: flex;
    align-items: center;
    gap: 10px;
    color: var(--brand-blue);
    font-weight: 600;
    letter-spacing: 1px;
    text-transform: uppercase;
  }
  .wordmark__dot {
    border-radius: 50%;
    background: var(--brand-blue);
    flex: none;
  }
  .card--front .wordmark {
    position: absolute;
    left: 0; right: 0; top: 0; bottom: 0;
    justify-content: center;
    font-size: 52px;
  }
  .card--front .wordmark__dot { width: 46px; height: 46px; }

  .back-art { position: absolute; inset: 0; }
  .card--back .wordmark {
    position: absolute;
    right: 26px;
    top: 128px;
    font-size: 30px;
    gap: 7px;
  }
  .card--back .wordmark__dot { width: 28px; height: 28px; }

  .contact {
    position: absolute;
    left: 26px;
    top: 26px;
    width: 230px;
    color: var(--ink-white);
  }
  .contact__name {
    font-size: 17px;
    font-weight: 600;
    letter-spacing: 1.5px;
    text-transform: uppercase;
  }
  .contact__role { font-size: 12px; margin-top: 2px; }
  .contact__address { font-size: 12px; line-height: 1.45; margin-top: 20px; }
  .contact__list { list-style: none; margin-top: 18px; font-size: 12px; }
  .contact__item {
    display: flex;
    align-items: center;
    gap: 8px;
    line-height: 1.8;
  }
  .contact__icon { width: 12px; height: 12px; flex: none; fill: none; stroke: var(--ink-white); stroke-width: 1.6; }
</style>
</head>
<body>

<section class="card card--front" aria-label="Card front">
  <div class="wordmark"><span>Kite Loft</span><span class="wordmark__dot"></span></div>
</section>

<section class="card card--back" aria-label="Card back">
  <svg class="back-art" viewBox="0 0 540 309" aria-hidden="true">
    <path d="M0 0 H300 C252 80 232 200 248 309 H0 Z" fill="var(--brand-blue)"/>
    <path d="M300 0 H330 C272 90 254 200 266 309 H248 C232 200 252 80 300 0 Z" fill="var(--swoosh-grey)"/>
  </svg>

  <div class="contact">
    <p class="contact__name">Corwin T. Aldous</p>
    <p class="contact__role">Managing Director</p>
    <p class="contact__address">27 Harbour Lane, Level 3<br>Dockside VIC</p>
    <ul class="contact__list">
      <li class="contact__item">
        <svg class="contact__icon" viewBox="0 0 12 12"><rect x="3" y="1" width="6" height="10" rx="1.2"/></svg>
        0431 587 904
      </li>
      <li class="contact__item">
        <svg class="contact__icon" viewBox="0 0 12 12"><rect x="1.5" y="4" width="9" height="5"/><rect x="3.5" y="1.5" width="5" height="2.5"/></svg>
        0431 587 904
      </li>
      <li class="contact__item">
        <svg class="contact__icon" viewBox="0 0 12 12"><rect x="1" y="2.5" width="10" height="7"/><path d="M1 2.5 L6 6.5 L11 2.5"/></svg>
        corwin@kiteloftdev.example
      </li>
      <li class="contact__item">
        <svg class="contact__icon" viewBox="0 0 12 12"><circle cx="6" cy="6" r="4.8"/><path d="M1.2 6 H10.8 M6 1.2 C3.5 4 3.5 8 6 10.8 M6 1.2 C8.5 4 8.5 8 6 10.8"/></svg>
        www.kiteloftdev.example
      </li>
    </ul>
  </div>

  <div class="wordmark"><span>Kite Loft</span><span class="wordmark__dot"></span></div>
</section>

</body>
</html>
```